Pull Up Banner - Recruitment Company

We would like a design for a pull up banner.

For context: we are a recruitment business. We specialise in helping people in healthcare industry to find jobs in Australia.

I have come up with several ideas and text for the banner. Feel free to use the following as you see appropriate:

- Our logo (see attached)
- 'Healthcare Recruitment Agency'
- Some sort of imagine / cartoon of medical professionals (ie. doctor, nurse, physiotherapist, speech pathologist). A cartoon is more friendly than committing to a photo
- 'Empowering your next career move'
- 'Discover tailored opportunities based on your career preferences'
- Dot points (allied health, nursing, medical imaging)
- Contact info at the bottom including our website (www.quellastaffing.com.au, our Instagram handle @quellastaffing, Mobile: XXXX XXX XXX. The title section for contact information could be 'Get in touch:'

Feel free to submit a couple of designs and we can merge aspects that look good on your designs and find the perfect fit.
Thank you
Updates

Hello,

Thank you for your initial submissions to this project. I appreciate the time you've invested.

After reviewing the first attempt, I'd like to share some feedback and initial observations:

- Professionalism and engagement: Is the overall appearance of the banner professional? It's crucial that we have a high-quality design as this will represent our business.

- Image selection: The image (whether cartoon or real people) appears quite generic. Please consider submitting the banner with a few different photos in the middle for us to choose from. Ensure the image is a good fit and not simply a generic stock photo.

- Contact section: Kindly remove the phone number; we no longer wish to include it on the banner. Instead, please include our website (www.quellastaffing.com.au) and Instagram handle (@quellastaffing).

- Color scheme: White, black, and red/pink are preferred, or alternatively, blue. However, please avoid incorporating too many different colors as it may detract from the professional appearance.

We will be printing the design on a banner and require it to look professional and engaging.

Thank you once again for your submissions. I hope the feedback provided above is helpful.

Warm regards,

Target Market(s)

Allied Health Australia

Font styles to use
Serif

Colors
0054AA
0677BA
7BADD7
CADEEF
E8F1F8
0094D4
00A9DD
6FCCEA
C7EBF8
E9F6FB
EB3D1F
EC4F4E
F09395
F8D3D4
FCEDEE

```html
<!DOCTYPE html>
<html lang="en">
<head>
<meta charset="utf-8">
<title>Quella Staffing – Pull Up Banner</title>
<link rel="stylesheet" href="https://fonts.googleapis.com/css2?family=Source+Serif+4:opsz,wght@8..60,400;8..60,600;8..60,700;8..60,800&display=swap">
<style>
  :root {
    --stage: #e9edf3;
    --banner-bg: #f4f6fa;
    --header-band: #dfe3ec;
    --ink: #1a1f2b;
    --accent: #1c3aa3;
    --photo-light: #eef1f6;
    --photo-mid: #cfd6e2;
    --photo-deep: #b3bccb;
  }
  * { margin: 0; padding: 0; box-sizing: border-box; }
  html, body { width: 1200px; height: 900px; overflow: hidden; }
  body {
    background: var(--stage);
    font-family: "Source Serif 4", Georgia, serif;
    color: var(--ink);
    display: flex;
    align-items: center;
    justify-content: center;
  }
  .banner {
    width: 340px;
    height: 870px;
    background: var(--banner-bg);
    display: flex;
    flex-direction: column;
    align-items: center;
    box-shadow: 0 6px 24px rgba(30, 40, 60, 0.12);
  }
  .banner-header {
    width: 100%;
    height: 124px;
    background: var(--header-band);
    display: flex;
    align-items: center;
    justify-content: center;
  }
  .brand-name {
    font-weight: 700;
    font-size: 34px;
    letter-spacing: 1px;
    color: var(--ink);
  }
  .tagline {
    margin-top: 30px;
    text-align: center;
    font-weight: 600;
    font-size: 17px;
    line-height: 1.3;
  }
  .headline {
    margin-top: 14px;
    text-align: center;
    font-weight: 600;
    font-size: 47px;
    line-height: 1.12;
    letter-spacing: -0.5px;
  }
  .headline .highlight { color: var(--accent); font-weight: 800; }
  .specialties {
    margin-top: 14px;
    width: 340px;
    height: 122px;
    flex-shrink: 0;
  }
  .specialties text {
    font-family: "Source Serif 4", Georgia, serif;
    font-weight: 700;
    font-size: 12px;
    fill: var(--ink);
  }
  .photo-area {
    width: 100%;
    flex: 1;
    margin-top: 4px;
    background: linear-gradient(180deg, var(--photo-light) 0%, var(--photo-mid) 40%, var(--photo-deep) 70%, var(--photo-light) 100%);
  }
  .contact {
    height: 96px;
    display: flex;
    flex-direction: column;
    align-items: center;
    justify-content: center;
    gap: 4px;
  }
  .contact-web { font-size: 14px; }
  .contact-web strong { font-size: 21px; font-weight: 600; }
  .contact-social { font-size: 21px; display: flex; align-items: center; gap: 8px; }
  .social-dot {
    width: 16px; height: 16px;
    border: 2px solid var(--accent);
    border-radius: 50%;
  }
</style>
</head>
<body>
  <main class="banner">
    <header class="banner-header">
      <span class="brand-name">Quella Staffing</span>
    </header>

    <p class="tagline">Healthcare<br>Recruitment Agency</p>

    <h1 class="headline">Empowering<br>your <span class="highlight">next</span><br><span class="highlight">career</span> move</h1>

    <svg class="specialties" viewBox="0 0 340 122" aria-label="Specialties: Allied Health, Nursing, Medical Imaging">
      <g fill="none" stroke="#1c3aa3" stroke-width="2.4">
        <polygon points="52,42 70,11 106,11 124,42 106,73 70,73"/>
        <polygon points="126,86 144,55 180,55 198,86 180,117 144,117"/>
        <polygon points="202,36 220,5 256,5 274,36 256,67 220,67"/>
      </g>
      <text x="88" y="39" text-anchor="middle">Allied</text>
      <text x="88" y="53" text-anchor="middle">Health</text>
      <text x="162" y="90" text-anchor="middle">Nursing</text>
      <text x="238" y="33" text-anchor="middle">Medical</text>
      <text x="238" y="47" text-anchor="middle">Imaging</text>
    </svg>

    <div class="photo-area" role="img" aria-label="Photo of a doctor at a desk reaching out for a handshake, with clipboard and laptop"></div>

    <footer class="contact">
      <p class="contact-web">www.<strong>quellastaffing</strong>.com.au</p>
      <p class="contact-social"><span class="social-dot"></span>@quellastaffing</p>
    </footer>
  </main>
</body>
</html>
```